Yacht, Boats, Watersports company needs a redesign of business card

Hello Designers!
We are a Boat dealership company that sells fun in the water, we sell boats, Yachts, Kayaks and also yacht WaterSport toys. We are looking to redesign our business cards in to something a little bit more sophisticated. in a way that we can make better use of our company colors. I'm attaching a zipped file containing the company 3 sets of company logo which one is an horizontal another one is a vertical and also a chromed 3d logo. Also is included two set of business cards that we use and also some designs that i think it's interesting. We use PMS 2026c Orange and PMS 7687C Blue. I would like to see at least two different options with the orange as accent and also using blue as an accent color. It's really important for the business cards to have a font option and size that is legible to most people. Our current website is wwww.coralpennant.com. Please visit if you want to have a better feeling of the Boat dealership
You can send Single sided or double side options. We are now using single sided but we may be open for a double side option if we really like the design.
Target Market(s)
Marine, boat sales, yacht sales, water toys sales/
Contact Information for Business Card
Name: Dale Whitcombe
Address: 212 North Fenwick Lane,
Dania Beach, FL 33004
Phone: 954-731-8842
Fax: 954:731-8843
Cell: 954-382-1490
Email: dw@coralpennant.com
Website: coralpennant.com
Requirements
Must have
- the current information of the business card provided.
logo
use the PMS Colors
Nice to have
- a touch of elegance and sophistication but simple
Should not have
- should not have any typography that is hard to read, the card should be simple but yet sophisticated.

```html
<!DOCTYPE html>
<html lang="en">
<head>
<meta charset="utf-8">
<title>Coral Pennant Marine Center – Business Card</title>
<link rel="stylesheet" href="https://fonts.googleapis.com/css2?family=Poppins:wght@400;500;600;700&display=swap">
<style>
  :root {
    --brand-blue: #1c64ae;
    --card-blue: #2069b3;
    --deep-blue: #174f8c;
    --brand-orange: #e9781f;
    --ink: #3a3a3a;
    --paper: #ffffff;
    --backdrop: #e6e8eb;
  }
  * { box-sizing: border-box; margin: 0; padding: 0; }
  html, body { width: 1200px; height: 900px; overflow: hidden; }
  body {
    background: var(--backdrop);
    font-family: "Poppins", sans-serif;
    position: relative;
  }
  .card {
    position: absolute;
    width: 660px;
    height: 380px;
    overflow: hidden;
    box-shadow: 0 6px 18px rgba(0,0,0,0.18);
  }
  /* Front */
  .card-front {
    left: 340px; top: 50px;
    background: var(--card-blue);
    display: flex; flex-direction: column; align-items: center; justify-content: center;
    gap: 18px;
  }
  .front-mark {
    width: 84px; height: 84px; border-radius: 50%;
    border: 6px solid var(--deep-blue);
  }
  .front-name {
    font-weight: 600; font-size: 34px; letter-spacing: 1px;
    color: var(--deep-blue); text-transform: uppercase; text-align: center;
    line-height: 1.15;
  }
  /* Back */
  .card-back {
    left: 190px; top: 480px;
    background: var(--paper);
  }
  .brand-block {
    position: absolute; left: 40px; top: 60px; width: 300px;
    display: flex; flex-direction: column; align-items: center; gap: 14px;
  }
  .brand-mark {
    width: 70px; height: 70px; border-radius: 50%;
    border: 6px solid var(--brand-blue);
  }
  .brand-name {
    font-weight: 600; font-size: 26px; color: var(--brand-blue);
    text-transform: uppercase; text-align: center; line-height: 1.15;
  }
  .divider {
    position: absolute; left: 362px; top: 50px; width: 2px; height: 170px;
    background: var(--brand-blue);
  }
  .contact {
    position: absolute; left: 390px; top: 48px; color: var(--ink);
  }
  .contact-name {
    font-weight: 700; font-size: 25px; color: var(--brand-blue);
    text-transform: uppercase; letter-spacing: 0.5px; margin-bottom: 6px;
  }
  .contact-address { font-size: 17px; line-height: 1.3; margin-bottom: 10px; }
  .contact-list { list-style: none; font-size: 17px; line-height: 1.4; }
  .contact-list li { display: flex; align-items: center; gap: 10px; }
  .contact-list svg { width: 15px; height: 15px; fill: var(--brand-blue); flex: none; }
  .band-blue {
    position: absolute; left: 0; top: 268px; width: 470px; height: 36px;
    background: var(--brand-blue);
  }
  .band-orange {
    position: absolute; left: 470px; top: 304px; right: 0; height: 34px;
    background: var(--brand-orange);
  }
  .band-mark {
    position: absolute; left: 448px; top: 281px; width: 44px; height: 44px;
    border-radius: 50%; background: var(--paper); border: 4px solid var(--brand-blue);
  }
  .website {
    position: absolute; left: 70px; top: 312px;
    font-size: 19px; letter-spacing: 2px; color: var(--brand-blue); font-weight: 500;
  }
</style>
</head>
<body>
  <section class="card card-front">
    <div class="front-mark"></div>
    <div class="front-name">Coral Pennant<br>Marine Center</div>
  </section>

  <section class="card card-back">
    <div class="brand-block">
      <div class="brand-mark"></div>
      <div class="brand-name">Coral Pennant<br>Marine Center</div>
    </div>
    <div class="divider"></div>
    <div class="contact">
      <p class="contact-name">Dale Whitcombe</p>
      <p class="contact-address">212 North Fenwick Lane<br>Dania Beach, FL 33004</p>
      <ul class="contact-list">
        <li><svg viewBox="0 0 24 24" aria-hidden="true"><path d="M6.6 10.8a15 15 0 0 0 6.6 6.6l2.2-2.2a1 1 0 0 1 1-.25 11.4 11.4 0 0 0 3.6.57 1 1 0 0 1 1 1V20a1 1 0 0 1-1 1A17 17 0 0 1 3 4a1 1 0 0 1 1-1h3.5a1 1 0 0 1 1 1c0 1.25.2 2.45.57 3.57a1 1 0 0 1-.25 1z"/></svg>954-731-8842</li>
        <li><svg viewBox="0 0 24 24" aria-hidden="true"><path d="M7 1h10a2 2 0 0 1 2 2v18a2 2 0 0 1-2 2H7a2 2 0 0 1-2-2V3a2 2 0 0 1 2-2zm0 3v14h10V4z"/></svg>954-382-1490</li>
        <li><svg viewBox="0 0 24 24" aria-hidden="true"><path d="M6 2h10l2 2v4H6zM3 9h18a1 1 0 0 1 1 1v8h-4v4H6v-4H2v-8a1 1 0 0 1 1-1zm5 7v4h8v-4z"/></svg>954:731-8843</li>
        <li><svg viewBox="0 0 24 24" aria-hidden="true"><path d="M2 5h20v14H2zm2 2v.5l8 5 8-5V7z"/></svg>dw@coralpennant.com</li>
      </ul>
    </div>
    <div class="band-blue"></div>
    <div class="band-orange"></div>
    <div class="band-mark"></div>
    <p class="website">www.CoralPennant.com</p>
  </section>
</body>
</html>
```